Harborview Estates Business Card for Apartment Buildings

Create business cards for resident managers who run apartment buildings. The audience is the public who are searching for apartment rentals, and current residents who live at the apartment building. Key design element will be incorporating the company logo, however, the logo cannot dominate. The building name and manager name are more important than the logo. Current business card design leaves little room for copy, so we may need to reduce the size on the current card to allow for more space for copy.

Target Market(s)

Adults 18-65 years of age, who are looking for an apartment rental, plus current residents who live at our apartment buildings.

Industry/Entity Type

Property Management

Contact Information for Business Card

A major design element will be use of the company logo. Important property and manager contact information must be part of the design. The size of the logo will need to be reduced to make room for building and manager contact copy.

Font styles to use
Sans Serif

Colors
3176b5
000000
959595
ffffff

Requirements
Must have
• 1) Incorporate the company logo.
• 2) Use the company colors (dark blue, black/grey, over white).
• 3) FEATURE THE BUILDING NAME
• 4) FEATURE THE MANAGER NAME
• 5) The company name is less important than BUILDING and MANAGER
• 6) Manager contact information
• **SEE ATTACHED CREATIVE BRIEF**
Nice to have
• 1) Back of card logo watermark
• 2) Ability to write notes on back of carfd
Should not have
• Avoid letting the company logo dominate the card, the building name and manager are more important than the company logo.

```html
<!DOCTYPE html>
<html lang="en">
<head>
<meta charset="utf-8">
<title>Harborview Estates – Resident Manager Card</title>
<link href="https://fonts.googleapis.com/css2?family=Bebas+Neue&family=Montserrat:wght@400;600&display=swap" rel="stylesheet">
<style>
  :root{
    --brand-blue:#3176b5;
    --deep-blue:#1d5a82;
    --ink:#3a3a3a;
    --grey:#959595;
    --paper:#ffffff;
    --backdrop:#e9e9e9;
  }
  html,body{margin:0;padding:0;width:1200px;height:1047px;overflow:hidden;background:var(--backdrop);}
  .card{
    position:absolute;left:100px;top:252px;width:1000px;height:543px;
    background:var(--paper);border-radius:22px;
    box-shadow:0 6px 24px rgba(0,0,0,.12);
    font-family:"Montserrat",sans-serif;color:var(--ink);
  }
  .brand{position:absolute;left:6px;top:44px;display:flex;align-items:center;gap:16px;}
  .brand-mark{width:92px;height:116px;background:var(--grey);}
  .brand-name{
    font-family:"Montserrat",sans-serif;font-weight:600;font-size:34px;
    color:var(--brand-blue);letter-spacing:1px;line-height:1.05;text-transform:uppercase;
  }
  .manager{position:absolute;right:46px;top:252px;text-align:right;}
  .manager-name{
    font-family:"Bebas Neue",sans-serif;font-size:48px;color:var(--deep-blue);
    letter-spacing:1px;line-height:1;margin:0;
  }
  .rule{position:absolute;left:180px;top:319px;width:540px;height:2px;background:var(--deep-blue);}
  .manager-title{position:absolute;right:46px;top:305px;font-size:22px;letter-spacing:.5px;}
  .contacts{position:absolute;left:180px;top:357px;margin:0;padding:0;list-style:none;}
  .contacts li{display:flex;align-items:center;height:30px;font-size:22px;letter-spacing:.5px;color:#555;}
  .contacts svg{width:14px;height:14px;margin-right:14px;fill:var(--grey);}
  .contacts .web-domain{color:var(--brand-blue);}
  .property{position:absolute;right:46px;top:417px;text-align:right;font-size:22px;line-height:30px;letter-spacing:.5px;margin:0;font-style:normal;}
</style>
</head>
<body>
  <div class="card">
    <div class="brand">
      <div class="brand-mark"></div>
      <div class="brand-name">Harborview<br>Estates LLC</div>
    </div>

    <div class="manager">
      <h1 class="manager-name">MARISOL DELGADO</h1>
    </div>
    <div class="rule"></div>
    <div class="manager-title">Resident Manager</div>

    <ul class="contacts">
      <li><svg viewBox="0 0 16 16"><path d="M3 1l3 3-2 2c1 2 4 5 6 6l2-2 3 3-2 2C7 15 1 9 1 3z"/></svg>555-310-4827</li>
      <li><svg viewBox="0 0 16 16"><path d="M4 0h8v16H4zM5.5 2v10h5V2zM7 13.5h2v1H7z" fill-rule="evenodd"/></svg>555-284-6093</li>
      <li><svg viewBox="0 0 16 16"><path d="M4 2h8v4H4zM1 7h14v6h-3v2H4v-2H1zM5 11v3h6v-3z" fill-rule="evenodd"/></svg>555-310-4800</li>
      <li><svg viewBox="0 0 16 16"><path d="M1 3h14v10H1zM2.5 4.5v.4L8 9l5.5-4.1v-.4zM2.5 6.6v5h11v-5L8 10.7z" fill-rule="evenodd"/></svg>marisol@harborviewest.com</li>
      <li><svg viewBox="0 0 16 16"><path d="M8 1a7 7 0 110 14A7 7 0 018 1zm0 1.5A5.5 5.5 0 002.6 7h10.8A5.5 5.5 0 008 2.5zM2.6 9A5.5 5.5 0 008 13.5 5.5 5.5 0 0013.4 9z" fill-rule="evenodd"/></svg>www.<span class="web-domain">harborviewest</span>.com</li>
    </ul>

    <address class="property">
      Bayside Court Apartments<br>
      2841 Linden Avenue<br>
      Rivermont, CA 90215
    </address>
  </div>
</body>
</html>
```